Plakate für ein Fest
Zielgruppe
Das Kessner Park ist ein Gewerbepark mit unterschiedlichen Mietern von Handwerker über Musiker bis hin zu Vermögensberatung. Wir veranstalten ein Fest für unsere Mieter und möchten dieses Plakat als Einladung nutzen.
Aufgabenstellung
Hintergrund schwarz, Logo verwenden
Get together
BBQ & Cocktails im Kessner Park
am 13.10.2023 ab 18 Uhr
Logo Band wild pebbles
Kinderbereich
Wir freuen uns darauf, alle Mieter mit Familien begrüßen zu dürfen! Auch an die Kleinen haben wir gedacht.

```html
<!DOCTYPE html>
<html lang="de">
<head>
<meta charset="utf-8">
<title>Kessner Park – Get together Plakat</title>
<link href="https://fonts.googleapis.com/css2?family=Source+Sans+3:wght@400;600&family=Yellowtail&family=Alfa+Slab+One&display=swap" rel="stylesheet">
<style>
  :root {
    --page-bg: #c4c4c2;
    --poster-black: #0c0c0c;
    --poster-white: #f2f2f2;
    --accent-green: #3fae5a;
    --doodle-grey: #1a1a1a;
  }
  * { box-sizing: border-box; margin: 0; padding: 0; }
  html, body {
    width: 1200px;
    height: 800px;
    overflow: hidden;
    background: var(--page-bg);
  }
  .poster {
    position: absolute;
    left: 331px;
    top: 20px;
    width: 537px;
    height: 760px;
    background: var(--poster-black);
    color: var(--poster-white);
    font-family: "Source Sans 3", sans-serif;
    overflow: hidden;
  }
  .doodle-backdrop {
    position: absolute;
    left: 0; top: 0;
    width: 100%; height: 695px;
    background: radial-gradient(ellipse at 50% 45%, var(--doodle-grey), var(--poster-black) 75%);
  }
  .brand {
    position: absolute;
    left: 36px;
    top: 34px;
    display: flex;
    align-items: center;
    gap: 14px;
  }
  .brand-mark {
    width: 52px;
    height: 52px;
    background: var(--accent-green);
  }
  .brand-name {
    font-family: "Source Sans 3", sans-serif;
    font-weight: 600;
    font-size: 38px;
    line-height: 40px;
    letter-spacing: 1px;
    text-transform: uppercase;
    color: var(--poster-white);
  }
  .event-script {
    position: absolute;
    left: 222px;
    top: 122px;
    font-family: "Yellowtail", cursive;
    font-size: 50px;
    color: var(--accent-green);
    transform: rotate(-17deg);
    transform-origin: left bottom;
    white-space: nowrap;
  }
  .event-type {
    position: absolute;
    left: 114px;
    top: 172px;
    width: 310px;
    padding: 3px 0 2px;
    border-top: 2px solid var(--poster-white);
    border-bottom: 2px solid var(--poster-white);
    font-family: "Alfa Slab One", serif;
    font-size: 25px;
    line-height: 28px;
    text-align: center;
    letter-spacing: 0.5px;
    color: var(--poster-white);
  }
  .centered {
    position: absolute;
    left: 0;
    width: 100%;
    text-align: center;
  }
  .event-date {
    top: 242px;
    font-size: 30px;
    letter-spacing: 0.2px;
  }
  .guest-label {
    top: 320px;
    font-size: 18px;
  }
  .guest-band {
    top: 348px;
    font-size: 40px;
    font-weight: 400;
    letter-spacing: 2px;
    color: var(--poster-white);
  }
  .kids-area {
    top: 486px;
    font-size: 31px;
  }
  .welcome-note {
    top: 561px;
    font-size: 19px;
    line-height: 27px;
    color: var(--accent-green);
  }
  .guests-band {
    position: absolute;
    left: 0;
    bottom: 0;
    width: 100%;
    height: 65px;
    background: linear-gradient(180deg, #d8d8d8, var(--poster-white));
  }
</style>
</head>
<body>
  <main class="poster">
    <div class="doodle-backdrop" role="img" aria-label="Dezente Skizzen von Cocktails, Grillspießen und Snacks auf schwarzem Grund"></div>

    <div class="brand">
      <span class="brand-mark"></span>
      <span class="brand-name">Kessner<br>Park</span>
    </div>

    <div class="event-script">get together</div>
    <div class="event-type">COCKTAILS &amp; BBQ</div>

    <p class="centered event-date">13. OKTOBER AB 18.00 UHR</p>
    <p class="centered guest-label">Special Guest:</p>
    <p class="centered guest-band">wild pebbles</p>

    <p class="centered kids-area">MIT KINDERBEREICH</p>

    <p class="centered welcome-note">
      Wir freuen uns darauf,<br>
      alle Mieter mit Familien begrüßen zu dürfen!<br>
      Auch an die Kleinen haben wir gedacht
    </p>

    <div class="guests-band" role="img" aria-label="Reihe weißer Silhouetten von Gästen am unteren Rand"></div>
  </main>
</body>
</html>
```